K & R Acre Works. Business card design

We need a business card designed for a new business. We have a bulldozer and tractor service. We clear land and make wildlife food plots. We provide disking, bush hogging, and site prep services.
I have attached an image of a business card that I like and would like my business cards to look similar.

Target Market(s)

anyone needing bulldozer and/or tractor services

Industry/Entity Type

Business

Contact Information for Business Card

K & R Acre Works, Operated by 7-T-Ranch
Wade Colton
601-472-3358
wcr4817@fieldmail-example.com

Font styles to use
Sans Serif

Colors

Designer to choose colors to be used in the design.

Requirements
Must have
• image of tractor and bulldozer
• Land Clearing
• Wildlife food plots
• Bush Hogging
• Disking
• Site prep
Nice to have
• i have included a image of a business card that i like. I would like mine to be similar.

```html
<!DOCTYPE html>
<html lang="en">
<head>
<meta charset="utf-8">
<title>K &amp; R Acre Works – Business Card</title>
<link rel="stylesheet" href="https://fonts.googleapis.com/css2?family=Roboto+Condensed:wght@400;500;700&family=Roboto:wght@400;500&display=swap">
<style>
  :root {
    --page-bg: #2c2c2c;
    --card-bg: #f3f3f1;
    --olive: #8d8a2b;
    --brown: #5e3814;
    --ink: #2f2f2f;
    --text-gray: #4a4a4a;
    --dozer-yellow: #d8c33a;
    --foliage: #5f7d3a;
    --tractor-orange: #e0562a;
  }
  * { margin: 0; padding: 0; box-sizing: border-box; }
  html, body {
    width: 1200px; height: 960px; overflow: hidden;
    background: var(--page-bg);
  }
  .card {
    position: absolute; left: 75px; top: 181px;
    width: 1050px; height: 599px;
    background: var(--card-bg);
    overflow: hidden;
    box-shadow: 0 4px 14px rgba(0,0,0,0.45);
    font-family: "Roboto", Arial, sans-serif;
  }
  .equipment-photo {
    position: absolute; left: 490px; top: 0; right: 0; bottom: 0;
    background:
      linear-gradient(180deg,
        #6f8a45 0%, var(--dozer-yellow) 18%, #c9b53a 34%, #6b5a3a 46%,
        var(--foliage) 52%, #4f6f32 64%, var(--tractor-orange) 80%, #c84a22 100%);
    -webkit-mask-image: linear-gradient(90deg, transparent 0%, rgba(0,0,0,0.6) 18%, #000 36%);
            mask-image: linear-gradient(90deg, transparent 0%, rgba(0,0,0,0.6) 18%, #000 36%);
  }
  .brand {
    position: absolute; left: 52px; top: 52px;
    display: flex; align-items: center; gap: 10px;
  }
  .brand-mark { width: 34px; height: 34px; background: var(--olive); }
  .brand-name {
    font-family: "Roboto Condensed", Arial, sans-serif;
    font-weight: 700; font-size: 34px; color: var(--brown);
    text-transform: uppercase; letter-spacing: 0.3px; line-height: 1;
  }
  .tagline {
    position: absolute; left: 52px; top: 98px;
    font-family: "Roboto Condensed", Arial, sans-serif;
    font-weight: 700; font-size: 17px; color: var(--ink);
    text-transform: uppercase; letter-spacing: 0.2px;
  }
  .edge-marks { position: absolute; left: 0; top: 186px; }
  .edge-marks span {
    display: block; width: 16px; height: 21px; margin-bottom: 5px;
    background: var(--olive);
  }
  .person-name {
    position: absolute; left: 52px; top: 162px;
    font-family: "Roboto Condensed", Arial, sans-serif;
    font-weight: 500; font-size: 36px; color: var(--olive);
    text-transform: uppercase;
  }
  .person-role {
    position: absolute; left: 52px; top: 212px;
    font-family: "Roboto Condensed", Arial, sans-serif;
    font-weight: 500; font-size: 26px; color: var(--brown);
    text-transform: uppercase;
  }
  .contact-list {
    position: absolute; left: 52px; top: 262px; list-style: none;
  }
  .contact-list li {
    display: flex; align-items: center; gap: 10px;
    height: 31.5px; font-size: 25px; color: var(--text-gray);
  }
  .contact-list svg { width: 21px; height: 21px; fill: var(--olive); flex: none; }
  .services-title {
    position: absolute; left: 52px; top: 386px;
    font-family: "Roboto Condensed", Arial, sans-serif;
    font-weight: 700; font-size: 30px; color: var(--olive);
    text-transform: uppercase;
  }
  .service-list {
    position: absolute; left: 52px; top: 425px; list-style: none;
  }
  .service-list li {
    height: 31.5px; font-size: 25px; color: var(--text-gray);
    display: flex; align-items: center;
  }
  .bullet {
    display: inline-block; width: 8px; height: 8px; border-radius: 50%;
    background: var(--olive); margin: 0 12px 0 2px;
  }
  .bullet.inline { margin: 0 6px 0 6px; }
</style>
</head>
<body>
  <div class="card">
    <div class="equipment-photo" role="img" aria-label="Photo of a yellow bulldozer pushing soil above an orange tractor with front loader in a green field"></div>

    <div class="brand">
      <span class="brand-mark"></span>
      <span class="brand-name">K &amp; R Acre Works</span>
    </div>
    <p class="tagline">For all of your land improvement needs</p>

    <div class="edge-marks"><span></span><span></span><span></span></div>

    <h1 class="person-name">Wade Colton</h1>
    <p class="person-role">Owner</p>

    <ul class="contact-list">
      <li>
        <svg viewBox="0 0 24 24" aria-hidden="true"><path d="M6.6 10.8a15.1 15.1 0 0 0 6.6 6.6l2.2-2.2c.3-.3.7-.4 1-.2 1.1.4 2.3.6 3.6.6.6 0 1 .4 1 1V20c0 .6-.4 1-1 1A17 17 0 0 1 3 4c0-.6.4-1 1-1h3.5c.6 0 1 .4 1 1 0 1.3.2 2.5.6 3.6.1.3 0 .7-.2 1z"/></svg>
        601-472-3358
      </li>
      <li>
        <svg viewBox="0 0 24 24" aria-hidden="true"><path d="M3 5h18v14H3z M4.5 6.5 12 12l7.5-5.5" fill="var(--olive)"/><path d="M4 6.5 12 12.5 20 6.5" fill="none" stroke="#f3f3f1" stroke-width="1.6"/></svg>
        wcr4817@fieldmail-example.com
      </li>
      <li>
        <svg viewBox="0 0 24 24" aria-hidden="true"><circle cx="12" cy="12" r="10"/><path d="M2 12h20M12 2c3 3 3 17 0 20M12 2c-3 3-3 17 0 20" fill="none" stroke="#f3f3f1" stroke-width="1.4"/></svg>
        kracreworks-example.com
      </li>
    </ul>

    <h2 class="services-title">We Creaded</h2>
    <ul class="service-list">
      <li><span class="bullet"></span>Land Clearing</li>
      <li><span class="bullet"></span>Wildlife food plots</li>
      <li><span class="bullet"></span>Bush Hogging</li>
      <li><span class="bullet"></span>Disking<span class="bullet inline"></span>Site prep</li>
    </ul>
  </div>
</body>
</html>
```